Cat-products company needs smart, yet endearing, business card

We need a business card design for a new, but up-and-running, business based in Honolulu, Hawaii. The business is Purrnest Nook Co. Our first product is the most environmentally-friendly cat grass kit ever seen on the planet. Future products, currently in the R&D phase, will include a variety of exciting cat scratchers. We also do consulting work to help apartment-dwellers make their home more cat-friendly and, in the future, plan on doing full, custom installs of structure to create high walkways for cats.

Target Market(s)

Middle-aged, apartment-dwelling, middle-class workers who own 1 or more cats and who dote on them.

Industry/Entity Type

Pet Care

Contact Information for Business Card

A striking, professional, yet warm and friendly design is what we're after.

Font styles to use
Serif
Sans Serif
Other font styles liked:
• Comfortaa

Colors

Designer to choose colors to be used in the design.

Requirements
Must have
• The company logo: (see attachment)
• The company name: Purrnest Nook Co
• The web address: www.purrnestnookco.com
• Email: support@purrnestnookco.com
• Phone: +1 (808) 571 6023
• Update (Fri Jun 30 3017 7:45pm Hawaii Time) I would like, is possible, uploaded picture of the cat grass kit on the back of the card with some text along the lines of: Purrnest Nook Co - Maker Of The Leafiest Feline Sprout Set Yet
Nice to have
• A cat picture, cartoon, real or silhouette that illustrates cats in action and/or relaxing; ie using the apartment space to live, play and relax in and being well-contented.
• Most of the website is done in the font: Comfortaa. It might be nice to continue using this for brand consistency.
Should not have
• Hard-to-read fonts.

```html
<!DOCTYPE html>
<html lang="en">
<head>
<meta charset="utf-8">
<title>Purrnest Nook Co — Business Card</title>
<link rel="stylesheet" href="https://fonts.googleapis.com/css2?family=Comfortaa:wght@700&family=Oswald:wght@400&family=Questrial&display=swap">
<style>
  :root {
    --backdrop: #e4e4e2;
    --card-white: #fbfbfa;
    --cocoa: #52302b;
    --marigold: #f0ab00;
    --ink-soft: #555150;
    --rule: #3f3a38;
  }
  * { margin: 0; padding: 0; box-sizing: border-box; }
  html, body {
    width: 1200px;
    height: 960px;
    overflow: hidden;
    background: var(--backdrop);
  }
  .stage {
    position: relative;
    width: 1200px;
    height: 960px;
  }
  .card {
    position: absolute;
    width: 600px;
    height: 343px;
    border-radius: 22px;
    box-shadow: 0 2px 5px rgba(0, 0, 0, 0.25);
  }
  .card--front {
    left: 314px;
    top: 113px;
    background: var(--card-white);
  }
  .card--back {
    left: 311px;
    top: 472px;
    background: var(--cocoa);
  }

  /* Front */
  .brand-mark {
    position: absolute;
    right: 34px;
    top: 52px;
    text-align: right;
    font-family: "Comfortaa", sans-serif;
    font-weight: 700;
    font-size: 33px;
    line-height: 1.1;
    color: var(--marigold);
  }
  .holder-name {
    position: absolute;
    left: 33px;
    top: 186px;
    font-family: "Oswald", sans-serif;
    font-weight: 400;
    font-size: 23px;
    letter-spacing: 0.3px;
    color: var(--cocoa);
  }
  .holder-role {
    position: absolute;
    left: 33px;
    top: 218px;
    font-family: "Questrial", sans-serif;
    font-size: 15px;
    letter-spacing: 0.4px;
    color: var(--marigold);
  }
  .divider {
    position: absolute;
    left: 33px;
    top: 243px;
    width: 534px;
    height: 1px;
    background: var(--rule);
  }
  .contact-list {
    position: absolute;
    left: 33px;
    top: 256px;
    list-style: none;
    font-family: "Questrial", sans-serif;
    font-size: 14.5px;
    color: var(--ink-soft);
  }
  .contact-list li {
    display: flex;
    align-items: center;
    height: 19px;
  }
  .contact-list svg {
    width: 12px;
    height: 12px;
    margin-right: 9px;
    fill: var(--cocoa);
  }
  .address {
    position: absolute;
    right: 33px;
    top: 275px;
    text-align: right;
    font-family: "Questrial", sans-serif;
    font-size: 14.5px;
    line-height: 19px;
    color: var(--ink-soft);
  }

  /* Back */
  .brand-mark--large {
    position: absolute;
    left: 0;
    right: 0;
    top: 132px;
    text-align: center;
    font-family: "Comfortaa", sans-serif;
    font-weight: 700;
    font-size: 40px;
    color: var(--card-white);
  }
  .social-row {
    position: absolute;
    left: 0;
    right: 0;
    top: 279px;
    display: flex;
    justify-content: center;
    gap: 4px;
    list-style: none;
  }
  .social-row li {
    width: 29px;
    height: 29px;
    border-radius: 50%;
    background: var(--marigold);
  }
</style>
</head>
<body>
  <main class="stage">
    <section class="card card--front" aria-label="Business card front">
      <div class="brand-mark">Purrnest<br>Nook Co</div>

      <h1 class="holder-name">LEILANI OKABE</h1>
      <p class="holder-role">CEO/FOUNDER</p>
      <div class="divider"></div>

      <ul class="contact-list">
        <li>
          <svg viewBox="0 0 12 12" aria-hidden="true"><path d="M2.4 0.5 L4.2 2.8 L3.2 4.2 C3.8 5.6 5.4 7.3 7.8 8.8 L9.2 7.8 L11.5 9.6 L10.3 11.5 C5.5 11.2 0.8 6.5 0.5 1.7 Z"/></svg>
          +1 (808) 571 6023
        </li>
        <li>
          <svg viewBox="0 0 12 12" aria-hidden="true"><path d="M0.5 2.5 H11.5 V3.2 L6 6.6 L0.5 3.2 Z M0.5 4.4 L6 7.8 L11.5 4.4 V9.5 H0.5 Z"/></svg>
          support@purrnestnookco.com
        </li>
        <li>
          <svg viewBox="0 0 12 12" aria-hidden="true"><path d="M6 0.5 A5.5 5.5 0 1 0 6.01 0.5 Z M3 3 C4 2.5 5 3.2 4.6 4.2 C4.2 5 5.5 5.6 5 6.6 C4.6 7.4 3.6 7 3.2 8 C2 6.6 1.8 4.4 3 3 Z M7.5 2 C9.2 2.6 10.4 4.4 10.2 6.4 C9.4 6.2 9 5.2 8 5.4 C7.2 5.6 6.8 4.4 7.4 3.8 C7.9 3.3 7.2 2.6 7.5 2 Z"/></svg>
          www.purrnestnookco.com
        </li>
      </ul>

      <address class="address">
        2219 Plumeria Court<br>
        Kailua, Hawaii 96734
      </address>
    </section>

    <section class="card card--back" aria-label="Business card back">
      <div class="brand-mark--large">Purrnest Nook Co</div>
      <ul class="social-row" aria-label="Social profiles">
        <li></li>
        <li></li>
        <li></li>
        <li></li>
      </ul>
    </section>
  </main>
</body>
</html>
```